Harbor Leaflet Ad

I need to create a layout with the information on the PDF, but I want you to re-design it and freshen up the look. I've attached a Word Doc with the size and format requirement for the harbor leaflet print. The PDF I created in illustrator CS6 also has the proper guides.

Target Market(s)

Storm Damaged Areas

Font styles to use
Serif
Sans Serif

Requirements
Must have
• Fresh, clean design. I prefer upscale look versus modern or techy.

```html
<!DOCTYPE html>
<html lang="en">
<head>
<meta charset="utf-8">
<title>Steady Crew Roofing – Harbor Leaflet Ad</title>
<link rel="stylesheet" href="https://fonts.googleapis.com/css2?family=Montserrat:wght@900&family=Oswald:wght@300;400;600;700&family=Roboto+Condensed:wght@300;400;700&display=swap">
<style>
  :root{
    --brown:#3b1a1c;
    --orange:#e8720c;
    --teal:#3d7c83;
    --concrete-light:#c9c9c9;
    --concrete-dark:#a9a9a9;
    --band:#d3d3d3;
    --white:#ffffff;
    --text:#2e2222;
    --coupon:#ececec;
  }
  *{box-sizing:border-box;margin:0;padding:0}
  html,body{width:1200px;height:958px;overflow:hidden;background:var(--white)}
  .ad-frame{position:absolute;left:124px;top:192px;width:952px;height:573px;background:var(--brown)}
  .ad-panel{position:absolute;left:27px;top:26px;width:898px;height:522px;border:1px solid var(--orange);overflow:hidden;
    background:radial-gradient(ellipse at 40% 40%,var(--concrete-light),var(--concrete-dark))}
  .bottom-band{position:absolute;left:0;top:408px;width:100%;height:114px;background:var(--band);opacity:.9}
  .hero-photo{position:absolute;left:305px;top:0;width:288px;height:522px;
    background:linear-gradient(180deg,#d64a2a 0%,#c98f75 14%,#c9a58e 22%,#2b3147 38%,#23293d 75%,#5b5f70 100%)}
  .headline{position:absolute;left:20px;top:32px;width:320px;text-align:center;font-family:"Montserrat",sans-serif;font-weight:900;letter-spacing:-3px;line-height:1}
  .headline .light{color:var(--white);font-size:46px;display:block}
  .headline .dark{color:var(--brown);font-size:57px;display:block;margin:-6px -20px -8px}
  .quote-url{position:absolute;left:37px;top:155px;font-family:"Oswald",sans-serif;font-weight:600;font-size:21.5px;color:var(--brown);letter-spacing:-.2px}
  .feature{position:absolute;top:195px;height:124px;padding:9px 4px 0 11px;border:1.5px solid}
  .feature--insured{left:35px;width:141px;border-color:var(--teal)}
  .feature--nailed{left:175px;width:118px;border-color:#9a5a1e}
  .feature h3,.feature p{font-family:"Oswald",sans-serif;font-weight:300;font-size:14px;line-height:17.5px;white-space:nowrap}
  .feature h3{color:var(--brown);text-transform:uppercase}
  .feature p{color:var(--text);font-size:13.5px}
  .feature svg{position:absolute;bottom:-10px;left:64px;width:14px;height:10px}
  .adjusters{position:absolute;left:35px;top:346px;width:250px}
  .adjusters h3{font-family:"Oswald",sans-serif;font-weight:300;font-size:14px;line-height:16px;color:var(--brown);text-transform:uppercase}
  .adjusters p{font-family:"Oswald",sans-serif;font-weight:300;font-size:13px;line-height:16px;color:var(--text)}
  .brand{position:absolute;left:41px;top:444px;display:flex;align-items:center;gap:10px}
  .brand-name{font-family:"Oswald",sans-serif;font-weight:700;font-size:50px;color:var(--brown);letter-spacing:-1px;line-height:1}
  .brand-dot{width:44px;height:44px;border-radius:50%;background:var(--orange)}
  .reviews{position:absolute;left:588px;top:20px;width:150px;text-align:center;color:var(--brown)}
  .reviews .mark{font-family:"Montserrat",sans-serif;font-weight:900;font-size:46px;line-height:30px;height:30px}
  .reviews h2{font-family:"Oswald",sans-serif;font-weight:700;font-size:19px;line-height:17px;text-transform:uppercase;margin-top:12px}
  .reviews hr{border:0;border-top:1px solid var(--brown);width:140px;margin:8px auto 8px}
  .reviews blockquote{font-family:"Roboto Condensed",sans-serif;font-size:7.6px;line-height:10px;text-align:justify;color:var(--text);width:138px;margin:0 auto}
  .reviews cite{font-style:normal;font-weight:700;margin-left:8px}
  .reviews .mark--close{margin-top:16px}
  .call{position:absolute;left:607px;top:356px;font-family:"Montserrat",sans-serif;font-weight:900;font-size:29px;letter-spacing:-1.5px;color:var(--brown)}
  .service-area{position:absolute;left:515px;top:395px;width:354px;height:34px;background:var(--orange);color:var(--white);
    font-family:"Oswald",sans-serif;font-weight:400;font-size:18px;line-height:34px;text-align:center;letter-spacing:-.2px}
  .coupons{position:absolute;left:753px;top:21px;width:118px}
  .coupon{position:absolute;left:0;width:118px;height:75px;background:var(--coupon);border:1px solid var(--orange);border-radius:4px;overflow:hidden}
  .coupon-tab{position:absolute;left:0;top:0;width:20px;height:100%;background:var(--orange)}
  .coupon-tab span{position:absolute;left:50%;top:50%;transform:translate(-50%,-50%) rotate(-90deg);white-space:nowrap;
    font-family:"Roboto Condensed",sans-serif;font-size:11px;color:var(--white)}
  .badge-accredited{position:absolute;left:516px;top:463px;width:114px;height:42px;border-radius:6px;background:#2a2224;border:2px solid var(--white)}
  .badge-rating{position:absolute;left:647px;top:470px;width:28px;height:28px;border-radius:50%;background:#2a2224}
  .badge-divider{position:absolute;left:690px;top:462px;width:1px;height:44px;background:var(--orange)}
  .badge-partner{position:absolute;left:709px;top:464px;width:42px;height:42px;background:#d9232e}
  .partner-label{position:absolute;left:763px;top:458px;font-family:"Oswald",sans-serif;font-weight:300;font-size:23px;line-height:24px;color:var(--brown)}
</style>
</head>
<body>
<div class="ad-frame">
  <div class="ad-panel">
    <div class="bottom-band"></div>
    <div class="hero-photo" role="img" aria-label="Photo of a smiling roofer in a red hard hat and navy sweater holding a small model house"></div>

    <h1 class="headline">
      <span class="light">Get a</span>
      <span class="dark">roof quote</span>
      <span class="light">online!</span>
    </h1>
    <div class="quote-url">www.steadycrewgc.com/roofquote</div>

    <div class="feature feature--insured">
      <h3>Fully-Insured<br>Roofing Crews</h3>
      <p>We carry both Liability<br>Coverage and Workers<br>Compensation for our<br>crews.</p>
      <svg viewBox="0 0 14 10"><path d="M0 0 L7 9 L14 0" fill="none" stroke="#3d7c83" stroke-width="1.5"/></svg>
    </div>
    <div class="feature feature--nailed">
      <h3>Quality, Hand<br>Nailed Roofs</h3>
      <p>Ask about our<br>professional<br>installation<br>process.</p>
      <svg viewBox="0 0 14 10"><path d="M0 0 L7 9 L14 0" fill="none" stroke="#e8720c" stroke-width="1.5"/></svg>
    </div>

    <div class="adjusters">
      <h3>Licensed Texas Property Adjusters</h3>
      <p>We have experience adjusting claims &amp; will help<br>you close your claim quickly.</p>
    </div>

    <div class="brand">
      <span class="brand-name">Steady Crew</span>
      <span class="brand-dot"></span>
    </div>

    <section class="reviews">
      <div class="mark">&ldquo;</div>
      <h2>See what your neighbors in North Texas are saying about us</h2>
      <hr>
      <blockquote>I am a very careful person when it comes to general contracting and especially roofing. Steady Crew put the roof on my mother's house after the last big hail storm we had. The foreman was at the site most of the time making sure he was there for the crew and for my mother as well. He worked well with the insurance adjuster and made sure all the paperwork was in order for the insurance company and the bank. You just don't see service like that often. They went on to do my neighbor's house as well. Both jobs were done professionally and look amazing. As long as Steady Crew is in business, I will keep referring them. <cite>-Mark T - Decatur, TX</cite></blockquote>
      <div class="mark mark--close">&rdquo;</div>
    </section>

    <div class="call">Call: 972 555 0148</div>
    <div class="service-area">LOCALLY OWNED COMPANY SERVICING NORTH TEXAS</div>

    <div class="coupons">
      <div class="coupon" style="top:0"><div class="coupon-tab"><span>Coupon #1</span></div></div>
      <div class="coupon" style="top:81px"><div class="coupon-tab"><span>Coupon #2</span></div></div>
      <div class="coupon" style="top:163px"><div class="coupon-tab"><span>Coupon #3</span></div></div>
      <div class="coupon" style="top:244px"><div class="coupon-tab"><span>Coupon #4</span></div></div>
    </div>

    <div class="badge-accredited"></div>
    <div class="badge-rating"></div>
    <div class="badge-divider"></div>
    <div class="badge-partner"></div>
    <div class="partner-label">PREFERRED<br>CONTRACTOR</div>
  </div>
</div>
</body>
</html>
```